Homemaking training schools needs a Business Card design

Designer, Hello!

No special requirements, good-looking enough.
--------------------------------------------------------------------------

Name: Marcus Dole
Chairman
Tel: 0574-71948263
Mobile: 13857420916
Email: kelvora@mailnest.example
Web: www.prt2019.example
Add: No.258, LanpingJie, BeiyuanQu, Ningbo, Zhejiang

LOGO
Ningbo PRT Homemaking Training School

Target Market(s)

pregnant women, mothers, infants, the elderly and families, including cleaning, cooking, nursing training.

Industry/Entity Type

Business

Contact Information for Business Card

Name: Marcus Dole
Chairman
Tel: 0574-71948263
Mobile: 13857420916
Email: kelvora@mailnest.example
Web: www.prt2019.example

LOGO

Font styles to use
Serif
Sans Serif
Decorative

Requirements
Nice to have
• Feels: clean, specifications, safety, comfort, warmth and happiness.

```html
<!DOCTYPE html>
<html lang="en">
<head>
<meta charset="utf-8">
<title>PeiRongTang Business Card</title>
<link rel="stylesheet" href="https://fonts.googleapis.com/css2?family=Lato:wght@400;700&family=Quicksand:wght@700&display=swap">
<style>
  :root {
    --brand-blue: #3a79bd;
    --brand-magenta: #c3178f;
    --ink: #1f1f1f;
    --paper: #ffffff;
    --backdrop: #e6e7ea;
    --card-w: 580px;
    --card-h: 331px;
  }
  html, body {
    margin: 0;
    width: 1200px;
    height: 900px;
    overflow: hidden;
    background: var(--backdrop);
  }
  .canvas {
    position: relative;
    width: 1200px;
    height: 900px;
  }
  .card {
    position: absolute;
    width: var(--card-w);
    height: var(--card-h);
    background: var(--paper);
    box-shadow: 0 10px 28px rgba(0,0,0,0.18);
    overflow: hidden;
  }
  .card--front { left: 540px; top: 80px; }
  .card--back  { left: 80px;  top: 470px; }

  .brand-name {
    margin: 0;
    font-family: "Lato", sans-serif;
    font-weight: 700;
    color: var(--ink);
  }
  .card--front .brand-name {
    position: absolute;
    left: 0; right: 0; top: 118px;
    text-align: center;
    font-size: 40px;
  }
  .front__web {
    position: absolute;
    left: 0; right: 0; top: 204px;
    margin: 0;
    text-align: center;
    font-family: "Lato", sans-serif;
    font-size: 15px;
    letter-spacing: 3px;
    color: var(--ink);
  }

  .back__wave { position: absolute; inset: 0; }
  .card--back .brand-name {
    position: absolute;
    left: 32px; top: 36px;
    font-size: 30px;
  }
  .person {
    position: absolute;
    right: 40px; top: 96px;
    font-family: "Lato", sans-serif;
  }
  .person__name {
    font-family: "Quicksand", sans-serif;
    font-weight: 700;
    font-size: 24px;
    color: var(--brand-blue);
    margin: 0;
  }
  .person__role {
    font-size: 15px;
    font-weight: 700;
    color: var(--ink);
    margin: 0;
  }
  .address {
    position: absolute;
    left: 32px; top: 235px;
    font-family: "Lato", sans-serif;
    font-size: 15px;
    line-height: 1.45;
    color: var(--paper);
    margin: 0;
    font-style: normal;
  }
  .contacts {
    position: absolute;
    right: 34px; top: 236px;
    list-style: none;
    margin: 0; padding: 0;
    font-family: "Lato", sans-serif;
    font-size: 15px;
    line-height: 1.4;
    color: var(--paper);
  }
  .contacts li { display: flex; align-items: center; gap: 10px; }
  .contacts svg { width: 13px; height: 13px; fill: var(--brand-magenta); flex: none; }
</style>
</head>
<body>
<main class="canvas">

  <section class="card card--front" aria-label="Business card front">
    <p class="brand-name">PeiRongTang</p>
    <p class="front__web">www.prt2019.example</p>
  </section>

  <section class="card card--back" aria-label="Business card back">
    <svg class="back__wave" viewBox="0 0 580 331" preserveAspectRatio="none" aria-hidden="true">
      <path d="M0,88 C150,150 300,178 420,182 C500,186 560,200 580,214 L580,331 L0,331 Z" fill="var(--brand-magenta)"/>
      <path d="M0,110 C150,170 300,198 420,202 C500,206 560,222 580,238 L580,331 L0,331 Z" fill="var(--paper)"/>
      <path d="M0,114 C150,174 300,202 420,206 C500,210 560,226 580,242 L580,331 L0,331 Z" fill="var(--brand-blue)"/>
    </svg>

    <p class="brand-name">PeiRongTang</p>

    <div class="person">
      <p class="person__name">Marcus Dole</p>
      <p class="person__role">Chairman</p>
    </div>

    <address class="address">No.258, LanpingJie<br>BeiyuanQu, Ningbo, Zhejiang</address>

    <ul class="contacts">
      <li>
        <svg viewBox="0 0 16 16" aria-hidden="true"><path d="M3 1h3l1.5 4-2 1.3a9 9 0 0 0 4.2 4.2L11 8.5l4 1.5v3a2 2 0 0 1-2 2A12 12 0 0 1 1 3a2 2 0 0 1 2-2z"/></svg>
        0574-71948263
      </li>
      <li>
        <svg viewBox="0 0 16 16" aria-hidden="true"><path d="M4 0h8a1 1 0 0 1 1 1v14a1 1 0 0 1-1 1H4a1 1 0 0 1-1-1V1a1 1 0 0 1 1-1zm1 2v10h6V2zm3 11a1 1 0 1 0 0 2 1 1 0 0 0 0-2z"/></svg>
        1385-7420916
      </li>
      <li>
        <svg viewBox="0 0 16 16" aria-hidden="true"><path d="M0 3h16v10H0zm1.5 1.2L8 9l6.5-4.8V4h-13z"/></svg>
        kelvora@mailnest.example
      </li>
      <li>
        <svg viewBox="0 0 16 16" aria-hidden="true"><path d="M8 0a8 8 0 1 0 0 16A8 8 0 0 0 8 0zm5.9 7h-2.9a12 12 0 0 0-1-4.9A6 6 0 0 1 13.9 7zM8 2c.8 1 1.4 2.8 1.5 5h-3C6.6 4.8 7.2 3 8 2zM6 2.1A12 12 0 0 0 5 7H2.1A6 6 0 0 1 6 2.1zM2.1 9H5a12 12 0 0 0 1 4.9A6 6 0 0 1 2.1 9zM8 14c-.8-1-1.4-2.8-1.5-5h3c-.1 2.2-.7 4-1.5 5zm2 -.1A12 12 0 0 0 11 9h2.9A6 6 0 0 1 10 13.9z"/></svg>
        www.prt2019.example
      </li>
    </ul>
  </section>

</main>
</body>
</html>
```